brightwell - Property Management DL Card

I am after a savvy designer to cut through junk mail! so many real estate agents use flyers to promote themselves and their business and usually sales. We are a property management firm (residential) and we want to represent landlords that have existing investment properties and need a quality agent to represent them. Can you help?
DL size, will be printed and delivered to mailboxes. For a look at our website go to www.brightwellrs.com.au. Keep it simple and clutter free.
it is to be double sided - with one side to be simple and clear - just our website, logo and telephone number on the back.
attached is our logo and our telephone number is 1300 48 92 16
the above are 2 essential elements to be included + our email address: admin@brightwellrs.com.au
also attached are our transparent price list

Target Market(s)
property investors,
people that manage properties themselves
Industry/Entity Type
Property Management
- arial
Look and feel

```html
<!DOCTYPE html>
<html lang="en">
<head>
<meta charset="utf-8">
<title>brightwell – Property Management DL Card</title>
<link rel="stylesheet" href="https://fonts.googleapis.com/css2?family=Open+Sans:wght@300;400;600&display=swap">
<style>
  :root {
    --stage: #e4e4e4;
    --frame-beige: #cbc6ba;
    --back-beige: #b2ab9b;
    --panel-white: #ffffff;
    --ink: #2e2b27;
    --ink-soft: #3f3b35;
    --bullet: #9a968f;
    --strip-dark: #1c1b19;
    --photo-dark: #4a3128;
    --photo-mid: #8c6a55;
    --photo-light: #e9e2d2;
  }
  * { margin: 0; padding: 0; box-sizing: border-box; }
  html, body { width: 1200px; height: 1200px; overflow: hidden; }
  body {
    background: var(--stage);
    font-family: "Open Sans", Arial, sans-serif;
    position: relative;
  }
  .card { position: absolute; left: 120px; width: 1000px; height: 500px; }
  .card-front { top: 58px; background: var(--frame-beige); }
  .card-back  { top: 637px; background: var(--back-beige); }

  .kitchen-photo {
    position: absolute; left: 0; top: 0; width: 667px; height: 500px;
    background: linear-gradient(180deg, var(--photo-light) 0%, #d8ccb8 35%, var(--photo-mid) 65%, var(--photo-dark) 100%);
  }
  .info-panel {
    position: absolute; left: 667px; top: 22px; width: 310px; height: 455px;
    background: var(--panel-white);
  }
  .tagline-strip {
    position: absolute; left: 465px; top: 118px; width: 495px; height: 26px;
    background: linear-gradient(90deg, rgba(28,27,25,0) 0%, rgba(28,27,25,0.85) 12%, var(--strip-dark) 60%, rgba(28,27,25,0) 100%);
    color: #f2f2f2; font-size: 18px; font-weight: 400; line-height: 26px;
    padding-left: 67px; letter-spacing: 0.2px;
  }
  .benefits {
    position: absolute; left: 695px; top: 156px; list-style: none;
    color: var(--ink); font-size: 16px; line-height: 21.5px;
  }
  .benefits li { position: relative; padding-left: 17px; }
  .benefits li::before {
    content: ""; position: absolute; left: 2px; top: 7px;
    width: 7px; height: 7px; background: var(--bullet); transform: rotate(45deg);
  }
  .brand-front {
    position: absolute; left: 667px; top: 385px; width: 320px; text-align: center;
    font-size: 40px; font-weight: 300; color: var(--ink); letter-spacing: -0.5px;
  }

  .brand-strip {
    position: absolute; left: 35px; top: 51px; width: 360px; height: 69px;
    background: linear-gradient(90deg, rgba(28,27,25,0) 0%, var(--strip-dark) 22%, var(--strip-dark) 70%, rgba(28,27,25,0) 100%);
    color: #f4f4f4; font-size: 34px; font-weight: 300; text-align: center; line-height: 69px;
  }
  .contact-block {
    position: absolute; left: 554px; top: 380px;
    border-left: 2px solid #6e675b; padding-left: 19px;
    color: var(--ink-soft); font-size: 18px; line-height: 24px; letter-spacing: 0.4px;
  }
</style>
</head>
<body>
  <section class="card card-front">
    <div class="kitchen-photo" role="img" aria-label="Photo of a bright modern kitchen with white cabinets, a dark island and timber floor"></div>
    <div class="info-panel"></div>
    <div class="tagline-strip">Property Management specialists</div>
    <ul class="benefits">
      <li>Excellent communication</li>
      <li>No hidden extras</li>
      <li>Minimal vacancy</li>
      <li>The best rent return</li>
    </ul>
    <div class="brand-front">brightwell</div>
  </section>

  <section class="card card-back">
    <div class="brand-strip">brightwell</div>
    <address class="contact-block" style="font-style:normal">
      1300 48 92 16<br>
      PO Box B392, Northgate NSW, 2164<br>
      admin@brightwellrs.com.au
    </address>
  </section>
</body>
</html>
```